Beacon Advisory Website

I currently have a website www.beaconadvisoryinc.com. We are a IT Consulting Company. Our website will pretty much tell out our services. I am looking to enhance my website and make it look more professional. Looking for very classy and Contemporary look and design for my website.

It Company

```html
<!DOCTYPE html>
<html lang="en">
<head>
<meta charset="utf-8">
<title>Beacon Advisory – IT Consulting</title>
<link href="https://fonts.googleapis.com/css2?family=Raleway:wght@400;500;600;700&family=Open+Sans:ital,wght@0,400;0,600;0,700;1,400&display=swap" rel="stylesheet">
<style>
  :root {
    --brand: #0b8fc7;
    --brand-bright: #12a8e0;
    --brand-deep: #1a5fa5;
    --footer-bar: #154c85;
    --nav-top: #1aa0d8;
    --nav-bottom: #0a78b4;
    --ink: #222831;
    --ink-soft: #555d66;
    --header-bg: #eef0f2;
    --band-grey: #e8ebee;
    --white: #ffffff;
    --line: #c9ced3;
  }
  * { box-sizing: border-box; margin: 0; padding: 0; }
  html, body { width: 672px; height: 1200px; overflow: hidden; }
  body { position: relative; font-family: "Open Sans", Arial, sans-serif; color: var(--ink); background: var(--white); }
  .abs { position: absolute; }

  /* Header */
  .site-header { position: absolute; left: 0; top: 0; width: 672px; height: 50px; background: linear-gradient(#f7f8f9, var(--header-bg)); border-top: 2px solid var(--brand); }
  .brand { position: absolute; left: 60px; top: 14px; display: flex; align-items: center; gap: 6px; font-family: "Raleway", sans-serif; font-weight: 700; font-size: 15px; color: var(--brand-deep); }
  .brand-dot { width: 18px; height: 18px; border-radius: 50%; background: var(--brand); }
  .contact-chip { position: absolute; top: 13px; display: flex; gap: 6px; }
  .contact-chip .chip-icon { width: 19px; height: 19px; border-radius: 50%; background: var(--brand-deep); display: flex; align-items: center; justify-content: center; margin-top: 2px; }
  .contact-chip .label { font-size: 7px; font-weight: 700; color: var(--brand-deep); line-height: 10px; }
  .contact-chip .value { font-size: 8.4px; color: var(--ink-soft); line-height: 11px; }

  /* Nav */
  .main-nav { position: absolute; left: 0; top: 50px; width: 672px; height: 24px; background: linear-gradient(var(--nav-top), var(--nav-bottom)); }
  .main-nav a { position: absolute; top: 0; height: 24px; line-height: 24px; font-size: 7.6px; font-weight: 700; color: var(--white); text-decoration: none; transform: translateX(-50%); }
  .main-nav .current { left: 60px; width: 62px; transform: none; text-align: center; background: var(--brand-bright); }
  .nav-divider { position: absolute; top: 5px; width: 1px; height: 14px; background: rgba(255,255,255,0.18); }

  /* Hero */
  .hero { position: absolute; left: 0; top: 74px; width: 672px; height: 228px; background: radial-gradient(circle at 72% 45%, #f4a42b 0%, #b35a10 12%, #3a1a08 30%, #0b0b0d 52%, #000 100%); }
  .hero-headline { position: absolute; left: 60px; top: 72px; width: 300px; font-family: "Raleway", sans-serif; font-weight: 700; font-size: 14.4px; line-height: 18.5px; color: var(--white); text-transform: uppercase; }
  .btn-read { position: absolute; left: 60px; top: 139px; width: 69px; height: 23px; background: var(--brand-bright); color: var(--white); font-size: 7px; font-weight: 700; line-height: 23px; padding-left: 12px; }

  /* Welcome */
  .welcome { position: absolute; left: 0; top: 302px; width: 672px; height: 108px; background: var(--brand); color: var(--white); text-align: center; }
  .welcome h1 { font-family: "Raleway", sans-serif; font-weight: 400; font-size: 17.5px; margin-top: 10px; }
  .welcome .rule { position: absolute; left: 200px; top: 38px; width: 272px; height: 1px; background: rgba(255,255,255,0.5); }
  .welcome p { position: absolute; left: 64px; top: 50px; width: 544px; font-size: 7.3px; line-height: 12.5px; color: #dbeff8; }
  .more-toggle { position: absolute; left: 324px; top: 93px; width: 24px; height: 15px; background: #3b3f44; border-radius: 2px 2px 0 0; color: var(--white); font-size: 13px; line-height: 15px; font-weight: 700; }

  /* Features */
  .feature { position: absolute; top: 436px; width: 180px; text-align: center; }
  .feature h3 { position: absolute; top: 104px; width: 180px; font-family: "Raleway", sans-serif; font-weight: 700; font-size: 10px; color: var(--ink); }
  .feature.is-active h3 { color: var(--brand); }
  .feature p { position: absolute; top: 120px; left: 10px; width: 160px; font-size: 7.4px; line-height: 9.6px; color: var(--ink-soft); }

  /* Services */
  .services { position: absolute; left: 0; top: 610px; width: 672px; height: 178px; background: var(--band-grey); }
  .section-title { position: absolute; width: 672px; text-align: center; font-family: "Raleway", sans-serif; font-weight: 400; font-size: 17.5px; color: var(--ink); }
  .section-title span { color: var(--brand); }
  .title-rule { position: absolute; left: 250px; width: 172px; height: 1px; background: var(--line); }
  .title-mark { position: absolute; left: 331px; width: 10px; height: 10px; border-radius: 50%; background: var(--brand); }
  .service-card { position: absolute; top: 60px; height: 94px; overflow: hidden; }
  .service-card .caption { position: absolute; left: 0; bottom: 0; width: 100%; height: 19px; background: rgba(20,90,160,0.85); color: var(--white); font-size: 10px; text-align: center; line-height: 19px; font-family: "Raleway", sans-serif; }
  .service-card.featured { background: #2a77b9; color: var(--white); text-align: center; }
  .featured h4 { font-family: "Raleway", sans-serif; font-weight: 700; font-size: 10.5px; margin-top: 13px; }
  .featured p { font-size: 6.4px; line-height: 9.6px; width: 140px; margin: 4px auto 0; font-weight: 600; }
  .featured .more { display: block; font-size: 6.2px; font-weight: 700; margin-top: 5px; }

  /* Testimonial */
  .testimonial-photo { position: absolute; left: 70px; top: 858px; width: 80px; height: 80px; border-radius: 50%; border: 3px solid #d3d6d9; background: linear-gradient(160deg, #c9b7a4, #6d7a8a 60%, #2b3a52); }
  .quote-text { position: absolute; left: 168px; top: 856px; width: 442px; font-size: 7.3px; line-height: 13.6px; font-style: italic; color: var(--ink-soft); text-align: center; }
  .quote-mark { position: absolute; font-family: Georgia, serif; font-size: 22px; color: #a7adb3; line-height: 1; }
  .quote-rule { position: absolute; left: 168px; top: 918px; width: 428px; height: 1px; background: #dde0e3; }
  .quote-author { position: absolute; left: 222px; top: 929px; font-size: 7.2px; font-weight: 700; color: var(--brand-deep); }
  .dots { position: absolute; left: 523px; top: 930px; display: flex; gap: 3px; }
  .dots i { width: 5px; height: 5px; border-radius: 50%; background: #c8ccd0; }
  .dots i.on { background: var(--brand); }

  /* Footer */
  .footer { position: absolute; left: 0; top: 1008px; width: 672px; height: 166px; background: var(--brand-deep); color: var(--white); }
  .footer h5 { position: absolute; top: 28px; font-family: "Raleway", sans-serif; font-weight: 600; font-size: 10px; }
  .quick-links { position: absolute; left: 59px; top: 50px; list-style: none; }
  .quick-links li { font-size: 6.8px; line-height: 21px; padding-left: 10px; position: relative; color: #dce8f5; }
  .quick-links li::before { content: ""; position: absolute; left: 1px; top: 9px; width: 3px; height: 3px; background: #dce8f5; }
  .contact-list { position: absolute; left: 159px; top: 48px; list-style: none; }
  .contact-list li { position: relative; padding-left: 13px; font-size: 6.6px; line-height: 9px; color: #dce8f5; margin-bottom: 11px; }
  .contact-list svg { position: absolute; left: 0; top: 1px; }
  .col-divider { position: absolute; top: 28px; width: 1px; height: 120px; background: rgba(255,255,255,0.08); }
  .field { position: absolute; left: 306px; width: 150px; border: 1px solid rgba(255,255,255,0.55); border-radius: 2px; font-size: 7px; color: #dce8f5; padding: 4px 7px; }
  .btn-submit { position: absolute; left: 306px; top: 133px; width: 58px; height: 18px; background: linear-gradient(#ffffff, #dfe3e7); border-radius: 2px; color: #334; font-size: 7.6px; text-align: center; line-height: 18px; }
  .footer-brand { position: absolute; left: 500px; top: 58px; display: flex; align-items: center; gap: 6px; font-family: "Raleway", sans-serif; font-weight: 700; font-size: 13px; color: var(--white); }
  .footer-brand .brand-dot { background: var(--white); width: 16px; height: 16px; }
  .social { position: absolute; top: 113px; width: 17px; height: 17px; border-radius: 2px; }
  .copyright { position: absolute; left: 0; top: 1174px; width: 672px; height: 26px; background: var(--footer-bar); color: #dce8f5; font-size: 7.2px; text-align: center; line-height: 26px; }
</style>
</head>
<body>

<header class="site-header">
  <div class="brand"><span class="brand-dot"></span>Beacon Advisory</div>
  <div class="contact-chip" style="left:375px;">
    <span class="chip-icon"><svg width="8" height="9" viewBox="0 0 8 9"><rect x="2" y="0.5" width="4" height="8" rx="1" fill="#fff"/></svg></span>
    <div><div class="label">CALL US</div><div class="value">+1 (555) 318 2760</div></div>
  </div>
  <div class="contact-chip" style="left:476px;">
    <span class="chip-icon"><svg width="10" height="8" viewBox="0 0 10 8"><rect x="0.5" y="0.5" width="9" height="7" fill="none" stroke="#fff"/><path d="M0.5 0.5 L5 4.5 L9.5 0.5" fill="none" stroke="#fff"/></svg></span>
    <div><div class="label">EMAIL US</div><div class="value">info@beaconadvisoryinc.com</div></div>
  </div>
</header>

<nav class="main-nav">
  <a class="current" href="#">HOME</a>
  <a href="#" style="left:167px;">ABOUT US</a>
  <span class="nav-divider" style="left:206px;"></span>
  <a href="#" style="left:245px;">SERVICES</a>
  <span class="nav-divider" style="left:284px;"></span>
  <a href="#" style="left:326px;">SOLUTIONS</a>
  <span class="nav-divider" style="left:369px;"></span>
  <a href="#" style="left:412px;">RESOURCES</a>
  <span class="nav-divider" style="left:455px;"></span>
  <a href="#" style="left:490px;">CAREER</a>
  <span class="nav-divider" style="left:526px;"></span>
  <a href="#" style="left:571px;">CONTACT US</a>
</nav>

<section class="hero" role="img" aria-label="Businessman holding a tablet with a glowing globe and small figures of people">
  <h2 class="hero-headline">Delivers highest level of quality consultants and services for the lowest cost of ownership</h2>
  <div class="btn-read">READ MORE</div>
</section>

<section class="welcome">
  <h1>Welcome To Beacon Advisoryinc</h1>
  <div class="rule"></div>
  <svg class="abs" style="left:330px;top:38px;" width="12" height="6"><path d="M0 0 L12 0 L6 6 Z" fill="#fff"/></svg>
  <p>Today's IT market is a dynamic, fast-paced industry, with ever-increasing demands. Meeting these demands for over 25 years, Beacon Advisory maintains a global presence, aggressively recruiting expertly qualified IT and Management Professionals from around the world and cultivating key partnerships with corporations to understand their business models end-to-end, with a goal of delivering exceptional client service and ensuring a consistent delivery....</p>
  <div class="more-toggle">+</div>
</section>

<svg class="abs" style="left:0;top:430px;" width="672" height="100" viewBox="0 430 672 100">
  <g fill="none" stroke="#555d66" stroke-width="0.8">
    <path d="M140 451 L150 443 L160 451"/><path d="M140 514 L150 522 L160 514"/>
    <path d="M116 475 L108 483 L116 491"/><path d="M184 475 L192 483 L184 491"/>
    <path d="M517 451 L527 443 L537 451"/><path d="M517 514 L527 522 L537 514"/>
    <path d="M494 475 L486 483 L494 491"/><path d="M560 475 L568 483 L560 491"/>
  </g>
  <g fill="none" stroke="#12a8e0" stroke-width="0.8">
    <path d="M326 439 L336 447 L346 439"/><path d="M326 522 L336 514 L346 522"/>
    <path d="M302 475 L310 483 L302 491"/><path d="M384 475 L376 483 L384 491"/>
  </g>
  <g fill="#2b2f35">
    <circle cx="143" cy="476" r="3"/><circle cx="157" cy="476" r="3"/>
    <rect x="139" y="480" width="8" height="8" rx="1"/><rect x="153" y="480" width="8" height="8" rx="1"/>
    <rect x="145" y="486" width="10" height="2"/><rect x="140" y="489" width="2" height="5"/><rect x="158" y="489" width="2" height="5"/>
  </g>
  <g fill="#0b8fc7">
    <circle cx="343" cy="481" r="8.5" fill="none" stroke="#0b8fc7" stroke-width="4" stroke-dasharray="3.4 2.3"/>
    <circle cx="343" cy="481" r="7"/><circle cx="343" cy="481" r="2.6" fill="#fff"/>
  </g>
  <rect x="516" y="471" width="22" height="24" rx="3" fill="#2b2f35"/>
</svg>

<div class="feature" style="left:60px;">
  <h3>CONSULTING</h3>
  <p>Beacon Advisory has certified professional consultants to work with you to help increase the business by providing IT services ...</p>
</div>
<div class="feature is-active" style="left:246px;">
  <h3>STAFF AUGMENTATION</h3>
  <p>For years Beacon Advisory as been offering our customers the ability to augment their existing staff..</p>
</div>
<div class="feature" style="left:437px;">
  <h3>OFFSHORE</h3>
  <p>Our Offshore development model has a unique distinction of providing efficient software solutions ...</p>
</div>

<section class="services">
  <h2 class="section-title" style="top:10px;">Our <span>Services</span></h2>
  <div class="title-rule" style="top:36px;"></div>
  <div class="title-mark" style="top:32px;"></div>
  <svg class="abs" style="left:28px;top:92px;" width="16" height="30"><path d="M14 1 L2 15 L14 29" fill="none" stroke="#9aa1a8" stroke-width="1"/></svg>
  <svg class="abs" style="left:626px;top:92px;" width="16" height="30"><path d="M2 1 L14 15 L2 29" fill="none" stroke="#9aa1a8" stroke-width="1"/></svg>

  <div class="service-card" style="left:60px;width:164px;background:linear-gradient(135deg,#0e2238,#2f4f73 55%,#b8c4d2);" role="img" aria-label="Hand touching a glowing network of technology icons">
    <div class="caption">Technology</div>
  </div>
  <div class="service-card featured" style="left:253px;width:165px;">
    <h4>OFFSHORE</h4>
    <p>Our Offshore development model has a unique distinction of providing efficient software solutions with cost and quality advantage, using state-of-the-art</p>
    <span class="more">READ MORE »</span>
  </div>
  <div class="service-card" style="left:446px;width:166px;background:linear-gradient(120deg,#2a6fa8,#6fb0d8 50%,#c7dbe8);" role="img" aria-label="Person tapping floating application icons">
    <div class="caption">Application Developement</div>
  </div>
</section>

<section class="testimonial">
  <h2 class="section-title" style="top:806px;">Client <span>Testimonial</span></h2>
  <div class="title-rule" style="top:834px;"></div>
  <div class="title-mark" style="top:830px;"></div>
  <div class="testimonial-photo" role="img" aria-label="Portrait photo of the client"></div>
  <span class="quote-mark" style="left:150px;top:852px;">“</span>
  <p class="quote-text">Lorem ipsum dolor sit amet, consectetuer adipiscing elit, sed diam nonummy nibh euismod tincidunt utvm laoreetm dolore magna aliquam erat volutpat. Ut wisi enim ad minim veniam, quis nostrud exerci tation ullamcorper suscipit lobortis nisl utmv aliquip ex ea commodo consequat. Duis autem vel eum iriure dolor in hendrerit in vulputate velit esse molestie consequat, velm illu dolore eu feugiat nulla facilisis at vero eros et accumsan etsto duis facilisi.</p>
  <span class="quote-mark" style="left:494px;top:896px;">”</span>
  <div class="quote-rule"></div>
  <svg class="abs" style="left:250px;top:918px;" width="8" height="5"><path d="M0 0 L8 0 L4 5 Z" fill="#dde0e3"/></svg>
  <div class="quote-author">- Miss Clara Whitfield</div>
  <div class="dots"><i class="on"></i><i></i><i></i><i></i></div>
</section>

<svg class="abs" style="left:0;top:920px;" width="672" height="90" viewBox="0 920 672 90">
  <path d="M0 1004 C 80 962, 200 952, 330 984 C 440 1010, 570 996, 672 946 L672 1010 L0 1010 Z" fill="#1a5fa5"/>
  <path d="M262 983 C 420 1016, 560 1000, 672 926 L672 944 C 565 1004, 420 1012, 262 983 Z" fill="#12a8e0"/>
</svg>

<footer class="footer">
  <h5 style="left:59px;">Quick Links</h5>
  <ul class="quick-links">
    <li>Home</li><li>About Us</li><li>Services</li><li>Resources</li><li>Contact Us</li>
  </ul>
  <span class="col-divider" style="left:146px;"></span>

  <h5 style="left:159px;">Contact Information</h5>
  <ul class="contact-list">
    <li><svg width="7" height="9" viewBox="0 0 7 9"><path d="M3.5 9 C1 5.5 0 4.2 0 3 A3.5 3.5 0 0 1 7 3 C7 4.2 6 5.5 3.5 9 Z" fill="#fff"/><circle cx="3.5" cy="3" r="1.2" fill="#1a5fa5"/></svg>240 Harbor Lane<br>Suite 12<br>Westbrook, NJ 07199</li>
    <li><svg width="8" height="8" viewBox="0 0 8 8"><path d="M1 0.5 L2.8 0.5 L3.4 2.4 L2.4 3.2 C3 4.4 3.6 5 4.8 5.6 L5.6 4.6 L7.5 5.2 L7.5 7 C4 7.5 0.5 4 1 0.5 Z" fill="#fff"/></svg>+1 (555) 318 2760</li>
    <li><svg width="9" height="8" viewBox="0 0 9 8"><rect x="2" y="0" width="5" height="2.5" fill="#fff"/><rect x="0" y="2.5" width="9" height="3.5" rx="0.8" fill="#fff"/><rect x="2" y="5" width="5" height="3" fill="#fff" stroke="#1a5fa5" stroke-width="0.6"/></svg>555.318.2761</li>
    <li><svg width="8" height="6" viewBox="0 0 8 6"><rect x="0" y="0" width="8" height="6" fill="#fff"/><path d="M0 0 L4 3.4 L8 0" fill="none" stroke="#1a5fa5" stroke-width="0.8"/></svg>office@beaconmail.com</li>
  </ul>
  <span class="col-divider" style="left:280px;"></span>

  <h5 style="left:306px;">Quick Contact</h5>
  <div class="field" style="top:44px;height:19px;">Name</div>
  <div class="field" style="top:67px;height:19px;">Phone</div>
  <div class="field" style="top:90px;height:34px;">Message</div>
  <div class="btn-submit">SUBMIT</div>
  <span class="col-divider" style="left:474px;"></span>

  <div class="footer-brand"><span class="brand-dot"></span>Beacon Advisory</div>
  <span class="social" style="left:504px;background:#1f3e7a;"></span>
  <span class="social" style="left:529px;background:#2f9ad3;"></span>
  <span class="social" style="left:553px;background:#1d7bbf;"></span>
  <span class="social" style="left:578px;background:#f09a1e;"></span>
</footer>

<div class="copyright">Copyright © 2016 Beaconadvisoryinc. All Rights Reserved.</div>

</body>
</html>
```